e-commerce store for sport clothing online store "baseball merchandise "web application...

I want to design a UX/UI for my web application website for the online store I will provide you with the following:
1. screen shots of the initial design for the pages>
2. the logo files.
3. The brand guideline file.

the provided files (screen shots) is guideline I want to see CREATIVITY with the UX/UI DESIGN.
PS. PLEASE FOLLOW THE BRANDGUIDE LINE CAREFULLY SPECIALLY THE TYPOGRAPHY & THE COLOR CODES.

PLEASE VISIT THIS WEBSITE brightlane.varomi-qz.com to see more for the screens.

```html
<!DOCTYPE html>
<html lang="en">
<head>
<meta charset="utf-8">
<title>Checkout – Order Confirmation</title>
<link href="https://fonts.googleapis.com/css2?family=Lato:wght@400;700;900&display=swap" rel="stylesheet">
<style>
  :root {
    --navy: #13224a;
    --navy-deep: #0f1c3d;
    --surface: #f4f5f7;
    --white: #ffffff;
    --ink: #1b1b1f;
    --ink-soft: #3a3f4b;
    --success: #27b23f;
    --black: #000000;
    --page-bg: #e9ebef;
    --scrim: rgba(0, 0, 0, 0.45);
  }
  * { box-sizing: border-box; margin: 0; padding: 0; }
  html, body {
    width: 930px; height: 1200px; overflow: hidden;
    background: var(--page-bg);
    font-family: "Lato", sans-serif;
    color: var(--ink);
  }
  .app-screen {
    position: absolute; left: 196px; top: 0;
    width: 537px; height: 1200px;
    background: var(--surface);
    overflow: hidden;
  }
  .top-bar {
    position: absolute; left: 0; top: 0; width: 100%; height: 125px;
    background: var(--navy-deep);
  }
  .top-bar .back { position: absolute; left: 36px; top: 50px; }
  .top-bar .title {
    position: absolute; left: 0; right: 0; top: 48px;
    text-align: center; color: var(--white);
    font-size: 25px; font-weight: 700;
  }
  .stepper { position: absolute; left: 0; top: 178px; width: 100%; height: 120px; }
  .stepper .rail {
    position: absolute; top: 29px; left: 117px; width: 303px; height: 2px;
    background: var(--navy);
  }
  .step { position: absolute; top: 0; width: 120px; margin-left: -60px; text-align: center; }
  .step .dot {
    width: 60px; height: 60px; border-radius: 50%; margin: 0 auto;
    background: var(--navy); color: var(--white);
    font-size: 28px; font-weight: 900; line-height: 60px;
  }
  .step .label { margin-top: 8px; font-size: 18px; line-height: 23px; color: var(--ink-soft); }
  .items-heading {
    position: absolute; left: 21px; top: 332px;
    font-size: 22px; font-weight: 700;
  }
  .item { position: absolute; left: 21px; width: 494px; height: 96px; }
  .item .thumb { position: absolute; left: 0; top: 0; width: 90px; height: 96px; border-radius: 6px; }
  .item .price {
    position: absolute; right: 0; top: 2px;
    font-size: 20px; font-weight: 900; color: var(--navy);
  }
  .thumb-shorts { background: linear-gradient(135deg, #b9754f, #4f9a63); }
  .thumb-cap { background: linear-gradient(135deg, #d7d9dc, #8d9096); }
  .totals { position: absolute; left: 30px; right: 30px; top: 930px; }
  .totals .row {
    display: flex; justify-content: space-between;
    font-size: 19px; line-height: 40px; color: var(--ink-soft);
  }
  .totals .row strong { color: var(--navy); font-weight: 900; }
  .action-bar {
    position: absolute; left: 0; right: 0; top: 1108px; height: 92px;
    background: var(--white);
  }
  .action-bar .place-order {
    position: absolute; left: 18px; right: 18px; top: 9px; height: 66px;
    background: var(--black); color: var(--white); border-radius: 6px;
    font-size: 21px; font-weight: 700; text-align: center; line-height: 66px;
  }
  .scrim { position: absolute; inset: 0; background: var(--scrim); }
  .dialog {
    position: absolute; left: 60px; top: 346px; width: 414px; height: 557px;
    background: var(--white); border-radius: 6px; text-align: center;
  }
  .dialog .close { position: absolute; right: 17px; top: 18px; }
  .dialog .badge { position: absolute; left: 155px; top: 85px; }
  .dialog h2 {
    position: absolute; left: 0; right: 0; top: 224px;
    font-size: 30px; font-weight: 700; color: var(--ink);
  }
  .dialog .message {
    position: absolute; left: 60px; right: 60px; top: 270px;
    font-size: 19px; line-height: 27px; color: var(--ink-soft);
  }
  .dialog .order-number {
    position: absolute; left: 0; right: 0; top: 373px;
    font-size: 19px; color: var(--ink-soft);
  }
  .dialog .continue {
    position: absolute; left: 80px; top: 461px; width: 256px; height: 65px;
    background: var(--navy); color: var(--white); border-radius: 5px;
    font-size: 21px; font-weight: 700; line-height: 65px;
  }
</style>
</head>
<body>
  <main class="app-screen">
    <header class="top-bar">
      <svg class="back" width="28" height="26" viewBox="0 0 28 26" aria-hidden="true">
        <path d="M26 13H3M13 2L2 13l11 11" fill="none" stroke="#fff" stroke-width="3" stroke-linecap="round" stroke-linejoin="round"/>
      </svg>
      <div class="title">Checkout</div>
    </header>

    <section class="stepper">
      <div class="rail"></div>
      <div class="step" style="left:117px"><div class="dot">1</div><div class="label">Shipping<br>Details</div></div>
      <div class="step" style="left:268px"><div class="dot">2</div><div class="label">Payment<br>Details</div></div>
      <div class="step" style="left:420px"><div class="dot">3</div><div class="label">Confirmation</div></div>
    </section>

    <h3 class="items-heading">Items</h3>
    <div class="item" style="top:387px">
      <div class="thumb thumb-shorts" role="img" aria-label="Product photo of patterned shorts"></div>
      <div class="price">25.000 KD</div>
    </div>
    <div class="item" style="top:532px">
      <div class="thumb thumb-cap" role="img" aria-label="Product photo of a grey baseball cap"></div>
      <div class="price">24.000 KD</div>
    </div>

    <section class="totals">
      <div class="row"><span>Subtotal</span><strong>49.000 KD</strong></div>
      <div class="row"><span>Delivery Charge</span><strong>1.000 KD</strong></div>
      <div class="row"><span>Total</span><strong>50.000 KD</strong></div>
    </section>

    <footer class="action-bar">
      <div class="place-order">Place Order</div>
    </footer>

    <div class="scrim"></div>

    <div class="dialog" role="dialog" aria-label="Order confirmation">
      <svg class="close" width="22" height="22" viewBox="0 0 22 22" aria-hidden="true">
        <path d="M3 3l16 16M19 3L3 19" stroke="#13224a" stroke-width="3" stroke-linecap="round"/>
      </svg>
      <svg class="badge" width="104" height="104" viewBox="0 0 104 104" aria-hidden="true">
        <circle cx="52" cy="52" r="52" fill="#27b23f"/>
        <path d="M29 53l16 16 31-33" fill="none" stroke="#fff" stroke-width="9" stroke-linecap="round" stroke-linejoin="round"/>
      </svg>
      <h2>Confirmation</h2>
      <p class="message">Your order has been placed successfully!</p>
      <p class="order-number">Order number is: 1223</p>
      <div class="continue">Continue Shopping</div>
    </div>
  </main>
</body>
</html>
```